I need a business card designed using the logo provided either vertical or horizontal......Harbourline Property Group is an Australian based real estate company that caters for the upper end of the market so the design of the business card "must reflect" the companies image!!
Colour combinations are optional but "must be realistic" and must be able to be accurately useable CMYK colours.
Please consider that any colours used "must be able to be used" and be suitable in following designs for "pull out banner signs" and "real estate signs".
The colours and the font in the attached designs are for example and other combinations are encouraged.
Target Market(s)
The High End of the Australian real estate market
Industry/Entity Type
Business
Contact Information for Business Card
Logo - Business Name - Director + Licensed Real Estate Agent - Mobile Number (Cell Phone) - Business Number - Fax - Email Address - Web address
Requirements
Must have
- Designs and colours (CMYK) that can easily be interpreted by an Australian printer.
Nice to have
- Some alternative ideas on colour and font..........the ones provided are ok and have been provided as an example but I am looking for alternative ideas
Should not have
- Loud, overly bright colours. Designs that do not reflect the professional standards of the business.
- Designs that look good on a computer monitor but can not be re-created on a printing press.............this is most important when it comes to shading etc.

```html
<!DOCTYPE html>
<html lang="en">
<head>
<meta charset="utf-8">
<title>Harbourline Property Group – Business Card</title>
<link rel="stylesheet" href="https://fonts.googleapis.com/css2?family=Open+Sans:wght@400;600;700&display=swap">
<style>
  :root {
    --backdrop: #3a3330;
    --card: #1c1c1c;
    --card-back: #161616;
    --gold: #c9962f;
    --gold-light: #e0b65a;
    --silver: #8e8e8e;
    --white: #f2f2f2;
    --text: #dcdcdc;
    --rule: #4a4a4a;
  }
  * { box-sizing: border-box; margin: 0; padding: 0; }
  html, body { width: 1200px; height: 844px; overflow: hidden; }
  body {
    background: var(--backdrop);
    font-family: "Open Sans", Arial, sans-serif;
    position: relative;
  }
  .card {
    position: absolute;
    width: 500px;
    height: 286px;
    border-radius: 4px;
    box-shadow: 0 10px 30px rgba(0,0,0,.45);
  }
  .card--front { left: 60px; top: 279px; background: var(--card); }
  .card--back  { left: 640px; top: 279px; background: var(--card-back);
    display: flex; align-items: center; justify-content: center; gap: 14px; }

  .brand { display: flex; align-items: center; gap: 12px; }
  .brand__mark { width: 22px; height: 22px; background: var(--gold); flex: none; }
  .brand__name {
    font-weight: 600; color: var(--silver);
    font-size: 22px; line-height: 1.1; letter-spacing: .5px;
  }
  .card--front .brand { position: absolute; left: 70px; top: 52px; }
  .card--back .brand__name { font-size: 26px; }

  .person { position: absolute; left: 40px; top: 162px; }
  .person__name { font-size: 21px; font-weight: 700; color: var(--white); }
  .person__title { font-size: 13px; color: var(--gold); margin-top: 1px; }
  .person__address { font-size: 13px; color: var(--text); margin-top: 10px; line-height: 1.35; }

  .divider {
    position: absolute; left: 258px; top: 150px;
    width: 1px; height: 96px; background: var(--rule);
  }

  .contact { position: absolute; left: 276px; top: 150px; list-style: none; }
  .contact__item {
    display: flex; align-items: center; gap: 10px;
    font-size: 13px; color: var(--text); height: 24px;
  }
  .contact__icon {
    width: 16px; height: 16px; background: var(--gold);
    border-radius: 2px; display: flex; align-items: center; justify-content: center; flex: none;
  }
  .contact__icon svg { width: 11px; height: 11px; }
</style>
</head>
<body>
  <section class="card card--front" aria-label="Business card front">
    <div class="brand">
      <span class="brand__mark"></span>
      <span class="brand__name">Harbourline<br>Property Group</span>
    </div>

    <div class="person">
      <p class="person__name">Daniel Whitmore</p>
      <p class="person__title">Managing Director</p>
      <p class="person__address">48 Esplanade Road<br>Sydney NSW 2000</p>
    </div>

    <span class="divider"></span>

    <ul class="contact">
      <li class="contact__item">
        <span class="contact__icon"><svg viewBox="0 0 12 12"><path d="M2 1h3l1 3-1.5 1a6 6 0 0 0 2.5 2.5L8 6l3 1v3a1 1 0 0 1-1 1A9 9 0 0 1 1 2a1 1 0 0 1 1-1z" fill="#1c1c1c"/></svg></span>
        (02) 9555 0148
      </li>
      <li class="contact__item">
        <span class="contact__icon"><svg viewBox="0 0 12 12"><rect x="3" y="1" width="6" height="10" rx="1" fill="#1c1c1c"/><rect x="4" y="2.5" width="4" height="6" fill="#c9962f"/></svg></span>
        0412 555 306
      </li>
      <li class="contact__item">
        <span class="contact__icon"><svg viewBox="0 0 12 12"><rect x="1" y="3" width="10" height="7" fill="#1c1c1c"/><path d="M1 3l5 4 5-4" stroke="#c9962f" fill="none"/></svg></span>
        info@harbourline.com.au
      </li>
      <li class="contact__item">
        <span class="contact__icon"><svg viewBox="0 0 12 12"><path d="M5 7l2-2M4 6L2.5 7.5a1.8 1.8 0 0 0 2.5 2.5L6.5 8.5M8 6l1.5-1.5A1.8 1.8 0 0 0 7 2L5.5 3.5" stroke="#1c1c1c" stroke-width="1.4" fill="none" stroke-linecap="round"/></svg></span>
        www.harbourline.com.au
      </li>
    </ul>
  </section>

  <section class="card card--back" aria-label="Business card back">
    <div class="brand">
      <span class="brand__mark"></span>
      <span class="brand__name">Harbourline<br>Property Group</span>
    </div>
  </section>
</body>
</html>
```